Business Card Design

My business is writing crime novels to entertain readers. I write legal thrillers and mysteries. I need a card for publishers, agents, other authors, and media.

Industry/Entity Type

Legal

Contact Information for Business Card

Paul Derrow
www.derrowfiction.example
pauljderrow@inkpost.example
0064 27 5190472

```html
<!DOCTYPE html>
<html lang="en">
<head>
<meta charset="utf-8">
<title>Paul Derrow — Business Card</title>
<link rel="stylesheet" href="https://fonts.googleapis.com/css2?family=Cabin+Condensed:wght@600&family=Cabin:wght@400&display=swap">
<style>
  :root {
    --page-bg: #d8d5d1;
    --card-light: #ffffff;
    --card-edge: #e6e6e6;
    --tape-yellow: #f5ea14;
    --ink: #0d0d0d;
    --frame-black: #111111;
    --photo-tone: #7a7a7a;
    --photo-tone-dark: #4a4a4a;
  }
  html, body {
    margin: 0;
    padding: 0;
    width: 1200px;
    height: 1181px;
    overflow: hidden;
    background: var(--page-bg);
  }
  .business-card {
    position: absolute;
    left: 50px;
    top: 274px;
    width: 1100px;
    height: 632px;
    box-shadow: 0 6px 18px rgba(0,0,0,0.25);
  }
  .business-card svg { display: block; width: 100%; height: 100%; }
  .tape-name {
    font-family: "Cabin Condensed", "Arial Narrow", sans-serif;
    font-weight: 600;
    font-size: 88px;
    fill: var(--ink);
  }
  .contact-line {
    font-family: "Cabin", "Gill Sans", sans-serif;
    font-size: 17px;
    fill: var(--ink);
  }
  .contact-bullet { fill: var(--ink); }
</style>
</head>
<body>
<div class="business-card">
  <svg viewBox="0 0 857 492" xmlns="http://www.w3.org/2000/svg">
    <defs>
      <radialGradient id="card-glow" cx="0.5" cy="0.45" r="0.7">
        <stop offset="0" stop-color="var(--card-light)"/>
        <stop offset="1" stop-color="var(--card-edge)"/>
      </radialGradient>
      <linearGradient id="portrait-tone" x1="0" y1="0" x2="0" y2="1">
        <stop offset="0" stop-color="var(--photo-tone)"/>
        <stop offset="1" stop-color="var(--photo-tone-dark)"/>
      </linearGradient>
      <clipPath id="card-clip"><rect width="857" height="492"/></clipPath>
      <filter id="soft-shadow" x="-10%" y="-10%" width="120%" height="130%">
        <feDropShadow dx="0" dy="3" stdDeviation="3" flood-opacity="0.3"/>
      </filter>
    </defs>

    <rect class="card-surface" width="857" height="492" fill="url(#card-glow)"/>

    <g clip-path="url(#card-clip)">
      <polygon class="portrait-backing" points="22,65 210,20 267,235 75,283" fill="var(--tape-yellow)" filter="url(#soft-shadow)"/>
      <rect class="portrait-frame" x="46" y="41" width="194" height="221" fill="var(--frame-black)" filter="url(#soft-shadow)"/>
      <g role="img" aria-label="Portrait photograph of author Paul Derrow">
        <rect x="52" y="47" width="182" height="209" fill="url(#portrait-tone)"/>
      </g>

      <g class="tape-band" transform="translate(0,405) rotate(-15)">
        <rect x="-80" y="-58" width="1020" height="116" fill="var(--tape-yellow)" filter="url(#soft-shadow)"/>
        <text class="tape-name" x="-436" y="32" textLength="480" lengthAdjust="spacingAndGlyphs">PAUL DERROW</text>
        <text class="tape-name" x="194" y="32" textLength="480" lengthAdjust="spacingAndGlyphs">PAUL DERROW</text>
        <text class="tape-name" x="824" y="32" textLength="480" lengthAdjust="spacingAndGlyphs">PAUL DERROW</text>

        <g class="contact-row">
          <rect class="contact-bullet" x="178" y="82" width="7" height="7" transform="rotate(45 181.5 85.5)"/>
          <text class="contact-line" x="194" y="92">0064 27 5190472</text>
          <rect class="contact-bullet" x="358" y="82" width="7" height="7" transform="rotate(45 361.5 85.5)"/>
          <text class="contact-line" x="374" y="92">pauljderrow@inkpost.example</text>
          <rect class="contact-bullet" x="614" y="82" width="7" height="7" transform="rotate(45 617.5 85.5)"/>
          <text class="contact-line" x="630" y="92">www.derrowfiction.example</text>
        </g>
      </g>
    </g>
  </svg>
</div>
</body>
</html>
```